TALVORNE End User Instruction Guide

I need to create a 5 to 7-page instruction guides for customers who purchased a phone system from our company. The document is a quick reference guide that will help end-users learn how to set up and use their new desk phone and software applications. I need the guide to be 3 x 5 or 6 x 8 in size and will fold like a book.

Target Market(s)

Business users / Quorblen Desk Phone Users / TalVORNE Portal users

Industry/Entity Type

Telecommunications

Font styles to use
Serif

Colors
0758a5
ffffff

Requirements
Must have
• Need to have step-by-step instructions that include the information from the QuickStart guide I provided. I need to see an image of the phone with an arrow pointing to the key on the phone that should be pressed. For example, when checking voicemail the Messages key is pressed and I want to highlight this button or call it out somehow.

I need to have three pages for setup instructions, one page for shortcuts or features codes and our support contacts on the last page.
Nice to have
• I want to have a page for notes that the end-user can use during training. I would also like to have a blank space next to passwords and user ID's so they can be filled out with specific details that are provided during their training. For example, in the voicemail section, I include a default PIN. I would like to leave this blank and let the end-user fill it out during training.
Should not have
• Complex shapes and designs. I like straight lines and a simple easy to understand layout.

```html
<!DOCTYPE html>
<html lang="en">
<head>
<meta charset="utf-8">
<title>TALVORNE Quick Reference – Using your desk phone</title>
<link rel="stylesheet" href="https://fonts.googleapis.com/css2?family=Roboto:ital,wght@0,400;0,500;0,700;1,400&display=swap">
<style>
  :root{
    --brand:#0758a5;
    --ink:#1b1b1b;
    --paper:#ffffff;
    --alert:#e0201b;
    --panel-dark:#2b2d31;
    --panel-mid:#45484e;
  }
  *{box-sizing:border-box;margin:0;padding:0}
  html,body{width:1200px;height:800px;overflow:hidden;background:var(--paper)}
  body{position:relative;font-family:'Roboto',Arial,sans-serif;color:var(--ink)}
  .rules{position:absolute;left:0;top:0}
  .t{position:absolute;white-space:nowrap;font-size:12px;line-height:15px}
  .brand{position:absolute;display:flex;align-items:center;gap:6px;color:var(--brand);font-weight:700;font-size:15px;letter-spacing:1px}
  .brand i{display:block;width:14px;height:14px;background:var(--brand)}
  .step-tag{position:absolute;left:31px;top:73px;width:115px;height:36px;background:var(--brand);color:var(--paper);font-weight:700;font-size:30px;line-height:36px;padding-left:4px;clip-path:polygon(0 0,92% 0,100% 100%,0 100%)}
  .page-title{position:absolute;left:230px;top:76px;font-size:27px;color:var(--brand);white-space:nowrap}
  .sec{position:absolute;white-space:nowrap;font-size:16px;line-height:18px;color:var(--brand);font-weight:500}
  .index{position:absolute;white-space:nowrap;font-size:12px;line-height:15px;font-weight:500;transform:translateX(-50%)}
  .b{font-weight:500}
  .hl{color:var(--brand);font-weight:700}
  .it{font-style:italic}
  .dot{position:absolute;width:7px;height:7px;border-radius:50%;background:var(--brand)}
  .num{position:absolute;width:15px;height:15px;border-radius:50%;background:var(--brand);color:var(--paper);font-size:11px;line-height:15px;text-align:center;font-weight:500}
  .phone{position:absolute;background:linear-gradient(135deg,var(--panel-mid),var(--panel-dark));border-radius:2px}
  .stars-title{position:absolute;left:887px;top:434px;transform:translateX(-50%);font-size:25px;font-style:italic;color:var(--brand);text-decoration:underline;white-space:nowrap}
  .sub{position:absolute;font-size:12px;font-weight:500;color:var(--brand);line-height:14px}
  .small{position:absolute;font-size:10.6px;line-height:13.5px;width:520px}
  .link{color:var(--brand)}
  .codes{position:absolute;left:632px;top:561px;width:511px;border-collapse:collapse;font-size:10.6px;line-height:12.5px}
  .codes th{background:var(--brand);color:var(--paper);font-weight:400;height:14px;padding:0 4px;border:1px solid var(--brand)}
  .codes td{border:1px solid var(--brand);padding:0 4px;vertical-align:middle}
  .codes td:first-child{width:93px}
  .codes tr.alert td{color:var(--alert);font-style:italic}
  .pg{position:absolute;top:762px;font-size:11px;background:var(--paper);padding:0 1px}
</style>
</head>
<body>

<svg class="rules" width="1200" height="800" viewBox="0 0 1200 800" aria-hidden="true">
  <g stroke="#0758a5" fill="#fff" stroke-width="1.3">
    <line x1="33" y1="73" x2="33" y2="800" stroke-width="3"/>
    <line x1="1165" y1="75" x2="1165" y2="800" stroke-width="3"/>
    <line x1="0" y1="770" x2="599" y2="770" stroke-width="3"/>
    <line x1="603" y1="770" x2="1200" y2="770" stroke-width="3"/>
    <line x1="35" y1="127" x2="242" y2="127"/><circle cx="245" cy="127" r="3"/>
    <line x1="35" y1="298" x2="238" y2="298"/><circle cx="241" cy="298" r="3"/>
    <line x1="35" y1="482" x2="238" y2="482"/><circle cx="241" cy="482" r="3"/>
    <line x1="35" y1="567" x2="238" y2="567"/><circle cx="241" cy="567" r="3"/>
    <circle cx="957" cy="77" r="3"/><line x1="960" y1="77" x2="1165" y2="77"/>
    <circle cx="1000" cy="171" r="3"/><line x1="1003" y1="171" x2="1165" y2="171"/>
    <circle cx="953" cy="244" r="3"/><line x1="956" y1="244" x2="1165" y2="244"/>
    <circle cx="980" cy="336" r="3"/><line x1="983" y1="336" x2="1165" y2="336"/>
  </g>
</svg>

<div class="brand" style="left:31px;top:33px"><i></i>TALVORNE</div>
<div class="brand" style="left:1043px;top:33px"><i></i>TALVORNE</div>

<div class="step-tag">STEP 3</div>
<h1 class="page-title" style="font-weight:400">Using your desk phone</h1>

<!-- Making calls -->
<div class="sec" style="left:268px;top:117px">Making Calls</div>
<div class="index" style="left:312px;top:134px">{XE "Calls:making"}</div>
<div class="t" style="left:56px;top:153px">Making a call with your phone does not require a leading 9. You can dial on-hook or off-hook.</div>
<div class="t b" style="left:56px;top:168px">To dial on-hook {XE "Dialing:on-hook"} {XE "On-hook dialing"}</div>
<div class="t" style="left:56px;top:183px">Dial the phone number.</div>
<div class="t" style="left:56px;top:198px">Pick up the handset, headset, or speaker.</div>
<div class="t b" style="left:56px;top:228px">To dial off-hook &nbsp;{XE "Dialing:off-hook"} {XE "Off-hook dialing"}</div>
<div class="t" style="left:56px;top:243px">Pick up the handset, headset, or speaker.</div>
<div class="t" style="left:56px;top:258px">Dial the phone number.</div>
<div class="t it" style="left:56px;top:273px">Calls to the US and Canada are all dialed using 10 or 11 digits.</div>

<!-- Receiving calls -->
<div class="sec" style="left:260px;top:289px">Receiving Calls</div>
<div class="index" style="left:312px;top:310px">{XE "Receiving calls"} {XE "Calls:receiving"}</div>
<div class="t" style="left:56px;top:329px">When a call comes in, you can answer it via a headset, speakerphone, or handset.</div>
<span class="dot" style="left:80px;top:347px"></span>
<div class="t b" style="left:99px;top:344px">To answer a call using a handset</div>
<div class="t" style="left:107px;top:359px">– Lift the handset off-hook.</div>
<span class="dot" style="left:80px;top:385px"></span>
<div class="t b" style="left:99px;top:382px">To answer a call using a speakerphone</div>
<div class="t" style="left:107px;top:397px">– Press the <span class="hl">Speaker</span> button.</div>
<span class="dot" style="left:80px;top:423px"></span>
<div class="t b" style="left:99px;top:420px">To answer a call using a headset</div>
<div class="phone" role="img" aria-label="Quorblen desk phone keypad with the Speaker key highlighted" style="left:387px;top:349px;width:182px;height:90px"></div>
<div class="t it" style="left:56px;top:442px">Usage depends on how the headset is connected. Often, you'll press the button on the headset or</div>
<div class="t it" style="left:56px;top:458px">press the headset button on the phone.</div>

<!-- Handling calls -->
<div class="sec" style="left:263px;top:473px">Handling Calls</div>
<div class="index" style="left:312px;top:494px">{XE "Handling calls"} {XE "Call handling"}</div>
<div class="t" style="left:56px;top:513px">Your cloud PBX features various ways to move calls around, including attended transfer,</div>
<div class="t" style="left:56px;top:528px">unattended (blind) transfer, voicemail transfer, park, and more. In this section, references to</div>
<div class="t" style="left:56px;top:543px">BLFs are the 1-touch buttons to extensions common at front-desk phones.</div>

<!-- Attended transfer -->
<div class="sec" style="left:251px;top:558px">Attended Transfer</div>
<div class="index" style="left:312px;top:580px">{XE "Transfers:attended"} {XE "Attended transfers"}</div>
<div class="t" style="left:56px;top:599px">Attended transfer allows you to speak to the transfer recipient prior to completing the transfer</div>
<div class="t" style="left:56px;top:614px">while the caller is on hold.</div>
<span class="dot" style="left:80px;top:647px"></span>
<div class="t b" style="left:99px;top:644px">To perform an attended transfer using Vantrel and Quorblen phones</div>
<span class="num" style="left:60px;top:670px">5</span>
<div class="t" style="left:83px;top:670px">Press the <span class="hl">Transfer</span> key/softkey on your phone.</div>
<span class="num" style="left:60px;top:692px">6</span>
<div class="t" style="left:83px;top:692px">Dial the recipient's extension or press their BLF.</div>
<span class="num" style="left:60px;top:714px">7</span>
<div class="t" style="left:83px;top:714px">Speak to the recipient, and then either press Transfer</div>
<div class="t" style="left:83px;top:729px">again to complete or cancel if the recipient cannot take</div>
<div class="t" style="left:83px;top:744px">the call.</div>
<div class="phone" role="img" aria-label="Quorblen desk phone keypad with the Transfer key highlighted" style="left:387px;top:663px;width:182px;height:90px"></div>

<span class="pg" style="left:29px">4</span>

<!-- Right page: blind transfer -->
<div class="sec" style="left:840px;top:66px">Blind Transfer</div>
<span class="dot" style="left:656px;top:87px"></span>
<div class="t b" style="left:675px;top:84px">To blind transfer using Quorblen phones</div>
<span class="num" style="left:636px;top:101px">8</span>
<div class="t" style="left:659px;top:101px">Press the <span class="hl">Transfer</span>.</div>
<span class="num" style="left:636px;top:123px">9</span>
<div class="t" style="left:659px;top:123px">Dial the extension of the recipient.</div>
<div class="t" style="left:659px;top:138px">Press Transfer</div>
<div class="phone" role="img" aria-label="Quorblen desk phone keypad with the Transfer key highlighted" style="left:983px;top:80px;width:182px;height:77px"></div>

<div class="sec" style="left:783px;top:162px">Transfers to External Numbers</div>
<div class="index" style="left:887px;top:184px">{XE "Transfers:external numbers"} {XE "External number transfers"}</div>
<div class="t" style="left:632px;top:202px">A transfer can also go to an external number such as a cell phone. Follow the transfer</div>
<div class="t" style="left:632px;top:217px">directions above but instead of dialing an extension, dial a 10-digit phone number.</div>

<div class="sec" style="left:840px;top:233px">Park and Hold</div>
<div class="index" style="left:887px;top:254px">{XE "Park and hold"}</div>
<span class="num" style="left:637px;top:275px">10</span>
<div class="t" style="left:659px;top:275px">Dial *** in an active call from any phone. The system says, “The call is parked at 7xx.”</div>
<span class="num" style="left:637px;top:294px">11</span>
<div class="t" style="left:659px;top:294px">Hang up.</div>
<div class="t" style="left:659px;top:309px">To retrieve the parked call, dial <span class="b">7xx</span> where <span class="b">xx</span> is the number stated by the system.</div>

<div class="sec" style="left:816px;top:326px">Emergency 911 Calls</div>
<span class="dot" style="left:633px;top:347px"></span>
<div class="t" style="left:643px;top:344px">When you dial 911 from ConnectLine running on a mobile phone, the application will</div>
<div class="t" style="left:643px;top:359px">automatically dial out using your existing cellular service. &nbsp;911 calls from your mobile</div>
<div class="t" style="left:643px;top:374px">phone will not be routed through your UCaaS service provider.</div>
<span class="dot" style="left:633px;top:396px"></span>
<div class="t" style="left:643px;top:393px">911 calls dialed from the desktop (WebRTC) app will be routed through your UCaaS service</div>
<div class="t" style="left:643px;top:408px">provider (the same as any other softphone).</div>

<h2 class="stars-title" style="font-weight:400">Star Codes and Features</h2>
<div class="sub" style="left:632px;top:461px">Concept</div>
<p class="small" style="left:632px;top:476px">Many features in the Corvanta platform are controlled by dialing the star key in conjunction with a 2 or 3 digit code. The default star codes are listed below. These may be customized per domain by the Halvex Control Tower.</p>
<div class="sub" style="left:632px;top:516px">Reserved Number Space</div>
<p class="small" style="left:632px;top:531px">Certain 3-4 digit extensions should NOT be used. Please be aware of the <span class="link">Reserved Number Space</span> page to avoid any conflicts with dial translations.</p>

<table class="codes">
  <thead><tr><th>Star Code</th><th>Feature Description</th></tr></thead>
  <tbody>
    <tr><td>***</td><td>Dynamically Park a Call (in the 701-709 range)</td></tr>
    <tr><td>*{parking lot}</td><td>Park a Call (to a specified park ext)</td></tr>
    <tr><td>*35{ext}</td><td>Extension Pickup - Answer a Call that is ringing at another extension</td></tr>
    <tr><td>*36</td><td>Domain Pickup - Answer a Call that is ringing within the same domain</td></tr>
    <tr><td>*37</td><td>Department Pickup - Answer a Call that is ringing within the same department</td></tr>
    <tr><td>*38</td><td>Self Pickup - Moves an active call to another extension owned by the Same User.<br>(Dial from the idle extension to steal the active call).</td></tr>
    <tr><td>*40</td><td>Activate Call Forwarding</td></tr>
    <tr><td>*41</td><td>Set Forward Busy Destination (This feature will only forward to Device or External<br>Number, forwarding to a user such as an Auto-Attendant must be done in the portal)</td></tr>
    <tr><td>*42</td><td>Set Forward No Answer Feature</td></tr>
    <tr><td>*44</td><td>Hotdesking (Log In) - Requires User Login and Password.</td></tr>
    <tr class="alert"><td>*45</td><td>Disable Call Forwarding (for Hotdesking). This star code is deprecated and no longer<br>needed for Hotdesking.</td></tr>
  </tbody>
</table>

<span class="pg" style="left:1161px">5</span>

</body>
</html>
```